Verdano Tiling Solutions, QBCC 4870312, ABN 28459106783, Email verdanotiling@tilebox-mail.com,Mobile 04159326

Verdano Tiling Solutions, is the name of my wall and floor tiling company and the details above are needed on the business card. Im open to see what people come up with i really have no colour requirements or other design specs as long as its not too plain.

```html
<!DOCTYPE html>
<html lang="en">
<head>
<meta charset="utf-8">
<title>Verdano Tiling Solutions – Business Card</title>
<link href="https://fonts.googleapis.com/css2?family=Exo+2:wght@400;600;700&display=swap" rel="stylesheet">
<style>
  :root {
    --canvas: #d9d9d9;
    --card-blue: #3f479f;
    --card-blue-deep: #2e3790;
    --card-blue-soft: #4a52a8;
    --card-white: #ffffff;
    --brand-red: #b5213f;
    --text-light: #ffffff;
    --shadow: rgba(0, 0, 0, 0.35);
  }
  * { margin: 0; padding: 0; box-sizing: border-box; }
  html, body {
    width: 1200px; height: 1000px; overflow: hidden;
    background: var(--canvas);
    font-family: "Exo 2", sans-serif;
  }
  .stage { position: relative; width: 1200px; height: 1000px; }
  .card {
    position: absolute; width: 429px; height: 264px; overflow: hidden;
    box-shadow: 3px 3px 4px var(--shadow);
  }
  .card--front { left: 206px; top: 147px; background: var(--card-white); }
  .card--back { left: 547px; top: 524px; }
  .tile-field {
    position: absolute; left: 0; top: 0; width: 100%;
    background:
      radial-gradient(ellipse at 30% 25%, var(--card-blue-soft) 0%, rgba(74, 82, 168, 0) 55%),
      radial-gradient(ellipse at 80% 85%, var(--card-blue-deep) 0%, rgba(46, 55, 144, 0) 60%),
      linear-gradient(135deg, var(--card-blue-soft) 0%, var(--card-blue) 50%, var(--card-blue-deep) 100%);
  }
  .card--front .tile-field { height: 165px; }
  .card--back .tile-field { height: 100%; }
  .holder-name {
    position: absolute; left: 223px; top: 28px;
    color: var(--text-light); font-weight: 600; font-size: 18px; letter-spacing: 0.5px;
  }
  .holder-role {
    position: absolute; left: 223px; top: 52px;
    color: var(--text-light); font-size: 11px;
  }
  .contact-list { position: absolute; left: 42px; top: 110px; list-style: none; }
  .contact-item {
    display: flex; align-items: center; gap: 5px;
    color: var(--text-light); font-size: 12px; height: 19px;
  }
  .contact-icon { width: 14px; height: 14px; }
  .brand-name {
    position: absolute; left: 0; width: 100%; text-align: center;
    font-weight: 700; text-transform: uppercase;
  }
  .card--front .brand-name {
    top: 182px; font-size: 24px; line-height: 28px; letter-spacing: 2px;
    color: var(--brand-red);
  }
  .card--back .brand-name {
    top: 92px; font-size: 31px; line-height: 36px; letter-spacing: 2.5px;
    color: var(--text-light);
  }
  .brand-name span { display: block; }
  .registration {
    position: absolute; left: 0; top: 176px; width: 100%; text-align: center;
    color: var(--text-light); font-size: 13px; font-weight: 600;
  }
  .registration span + span { margin-left: 14px; }
</style>
</head>
<body>
<main class="stage">
  <section class="card card--front">
    <div class="tile-field" role="img" aria-label="Blue decorative tile pattern background"></div>
    <h1 class="holder-name">Marco Verdani</h1>
    <p class="holder-role">Owner/ Founder</p>
    <ul class="contact-list">
      <li class="contact-item">
        <svg class="contact-icon" viewBox="0 0 14 14" aria-hidden="true">
          <rect x="1" y="0" width="12" height="14" rx="2" fill="#fff"/>
          <rect x="4" y="2" width="6" height="6" fill="#3f479f"/>
          <rect x="4" y="10" width="6" height="2" fill="#3f479f"/>
        </svg>
        04159326
      </li>
      <li class="contact-item">
        <svg class="contact-icon" viewBox="0 0 14 14" aria-hidden="true">
          <rect x="0" y="1" width="14" height="12" rx="2" fill="#fff"/>
          <rect x="2.5" y="3.5" width="9" height="7" fill="none" stroke="#3f479f" stroke-width="1"/>
          <path d="M2.5 3.5 L7 7.5 L11.5 3.5" fill="none" stroke="#3f479f" stroke-width="1"/>
        </svg>
        verdanotiling@tilebox-mail.com
      </li>
    </ul>
    <p class="brand-name"><span>Verdano</span><span>Tiling Solutions</span></p>
  </section>

  <section class="card card--back">
    <div class="tile-field" role="img" aria-label="Blue decorative tile pattern background"></div>
    <p class="brand-name"><span>Verdano</span><span>Tiling Solutions</span></p>
    <p class="registration"><span>QBCC 4870312</span><span>ABN 28459106783</span></p>
  </section>
</main>
</body>
</html>
```